Australian Trucking Company Requires Professional Looking Stationary

We require a professional looking stationary design that incorporates our newly designed logo.

Our business, called "Brell Haulage Contracting", provides contracting work, transport and logistics to business in Western Australia particularly with links to the mining sector.

We are a small business looking to expand and our new logo and our new stationary will help develop our brand image in our market place.

Target Market(s)

Businesses and Corporation with links to the Mining Sector

Industry/Entity Type

Small Business

Requirements
Must have
• The letterhead must have the following details:
The new logo

Text saying: "Brell Holdings Pty Ltd (ACN 582 316 907) ATF The Brell Discretionary Trust T/AS"
"ABN 71 834 209 553"
Address "P.O Box 817 Wattlegrove WA, 6958"
Phone: 08 9352 7140
Email: brellhaul@mailbox-example.com.au

The text on the letterhead should be editable as the details are likely to change in the near future. Provision should be made for a website address all though one isn't available at the moment.

The styling, layout and font text is entirely up to the designer.

```html
<!DOCTYPE html>
<html lang="en">
<head>
<meta charset="utf-8">
<title>Brell Haulage Contracting – Business Card</title>
<link rel="stylesheet" href="https://fonts.googleapis.com/css2?family=Open+Sans:wght@400;600;700&display=swap">
<style>
  :root {
    --backdrop: #e9e6e2;
    --card: #ffffff;
    --brand-red: #ec1c24;
    --brand-deep: #a3141b;
    --rule-grey: #a7a9ac;
    --ink: #3a3a3a;
    --ink-soft: #4d4d4d;
    --mark-grey: #8c8c8c;
  }
  * { box-sizing: border-box; margin: 0; padding: 0; }
  html, body {
    width: 1200px; height: 426px; overflow: hidden;
    background: var(--backdrop);
    font-family: "Open Sans", Arial, sans-serif;
    color: var(--ink);
  }
  .canvas { position: relative; width: 1200px; height: 426px; }
  .card {
    position: absolute; top: 62px; width: 518px; height: 296px;
    background: var(--card); border-radius: 20px; overflow: hidden;
    box-shadow: 0 2px 6px rgba(0,0,0,.18);
  }
  .card--front { left: 64px; }
  .card--back { left: 610px; }
  .front-art { position: absolute; inset: 0; }
  .brand-mark {
    position: absolute; left: 84px; top: 46px; width: 60px; height: 60px;
    background: var(--mark-grey);
  }
  .brand-name {
    position: absolute; left: 166px; top: 42px;
    font-weight: 700; font-size: 25px; line-height: 28px;
    color: var(--brand-deep); text-transform: uppercase; letter-spacing: .5px;
  }
  .contact-name {
    position: absolute; left: 173px; top: 154px;
    font-size: 16px; font-weight: 600; color: var(--ink);
  }
  .contact-name .role { font-size: 12px; font-weight: 400; }
  .contact-line {
    position: absolute; left: 173px; font-size: 12px; color: var(--ink-soft);
    display: flex; align-items: center; gap: 4px; white-space: nowrap;
  }
  .contact-line svg { width: 11px; height: 11px; fill: var(--brand-red); flex: none; }
  .contact-line .gap { width: 10px; }
  .line-phone { top: 186px; }
  .line-post { top: 207px; }
  .legal {
    position: absolute; left: 171px; font-size: 10.5px; color: #222;
    white-space: nowrap;
  }
  .legal-1 { top: 250px; }
  .legal-2 { top: 266px; }
  .legal-abn { position: absolute; left: 394px; top: 266px; font-size: 10.5px; color: #222; }
  .back-name {
    position: absolute; left: 0; right: 0; top: 128px; text-align: center;
    font-weight: 700; font-size: 30px; color: #111; text-transform: uppercase;
  }
</style>
</head>
<body>
<main class="canvas">
  <section class="card card--front" aria-label="Business card front">
    <svg class="front-art" width="518" height="296" viewBox="0 0 518 296" aria-hidden="true">
      <rect x="0" y="0" width="58" height="296" fill="var(--brand-red)"/>
      <rect x="61" y="0" width="5" height="296" fill="var(--rule-grey)"/>
      <polygon points="64,35 150,35 150,128 24,128" fill="#ffffff"/>
    </svg>
    <div class="brand-mark" aria-hidden="true"></div>
    <div class="brand-name">Brell<br>Haulage<br>Contracting</div>

    <p class="contact-name">Persons name, <span class="role">Manager</span></p>
    <p class="contact-line line-phone">
      <svg viewBox="0 0 24 24" aria-hidden="true"><path d="M6.6 10.8a15.1 15.1 0 0 0 6.6 6.6l2.2-2.2a1 1 0 0 1 1-.25 11.4 11.4 0 0 0 3.6.57 1 1 0 0 1 1 1V20a1 1 0 0 1-1 1A17 17 0 0 1 3 4a1 1 0 0 1 1-1h3.5a1 1 0 0 1 1 1c0 1.25.2 2.45.57 3.57a1 1 0 0 1-.25 1z"/></svg>
      <span>08 9352 7140</span>
      <span class="gap"></span>
      <svg viewBox="0 0 24 24" aria-hidden="true"><path d="M2 5h20v14H2z M4 7v.5l8 5 8-5V7z" fill-rule="evenodd"/></svg>
      <span>brellhaul@mailbox-example.com.au</span>
    </p>
    <p class="contact-line line-post">
      <svg viewBox="0 0 24 24" aria-hidden="true"><path d="M12 3 2 12h3v9h5v-6h4v6h5v-9h3z"/></svg>
      <span>P.O Box 817 Wattlegrove WA, 6958</span>
    </p>

    <p class="legal legal-1">Brell Holdings Pty Ltd (ACN 582 316 907)</p>
    <p class="legal legal-2">ATF The Brell Discretionary Trust T/AS</p>
    <p class="legal-abn">ABN 71 834 209 553</p>
  </section>

  <section class="card card--back" aria-label="Business card back">
    <p class="back-name">Brell Haulage Contracting</p>
  </section>
</main>
</body>
</html>
```